Casino with the 'highest winning percentage' needs a stationery design

This is for a casino in Colombo, Sri Lanka and we need a stationery design for business card, letter head and envelope.

Should be very professional, simple and elegant without fancy fonts

Reason: Not fully satisfied with the designs. Need more designs.

Business

• 1. card deck symbol 'CLUBS' in red, or black

2. name in BLOCK CAPITAL LETTERS

3. Preferred font colours are black, white or red

4. Prefer 'professional /elegant' fonts
• SHOULD NOT HAVE ANY OTHER SYMBOL EXCEPT 'CLUBS'

DO NOT PREFER ITALIC FONTS

```html
<!DOCTYPE html>
<html lang="en">
<head>
<meta charset="utf-8">
<title>Marlow's Entertainment – Stationery</title>
<link rel="stylesheet" href="https://fonts.googleapis.com/css2?family=Noto+Serif:wght@700&family=Open+Sans:wght@300;400;600&display=swap">
<style>
  :root {
    --red: #d3232f;
    --ink: #111111;
    --grey: #555555;
    --rule: #333333;
    --paper: #ffffff;
    --paper-shade: #eeeeee;
    --backdrop: #e7e3de;
    --black: #0c0c0c;
  }
  * { box-sizing: border-box; margin: 0; padding: 0; }
  html, body { width: 1200px; height: 385px; overflow: hidden; }
  body { background: var(--backdrop); font-family: "Open Sans", Arial, sans-serif; color: var(--ink); }
  .canvas { position: relative; width: 1200px; height: 385px; }

  .sheet {
    position: absolute; top: 20px; width: 262px; height: 338px;
    background: linear-gradient(160deg, var(--paper) 40%, var(--paper-shade));
    box-shadow: 0 1px 4px rgba(0,0,0,.25);
  }
  .sheet--plain { left: 8px; }
  .sheet--letter { left: 286px; }
  .sheet--fax { left: 559px; }

  .brand { position: absolute; display: flex; align-items: center; gap: 6px; }
  .brand__dot { width: 22px; height: 22px; border-radius: 50%; background: var(--red); flex: none; }
  .brand__name {
    font-family: "Noto Serif", Georgia, serif; font-weight: 700; color: var(--ink);
    font-size: 9px; line-height: 1.2; letter-spacing: .2px;
  }
  .sheet--plain .brand { left: 76px; top: 12px; }
  .sheet--letter .brand, .sheet--fax .brand { left: 10px; top: 12px; }

  .contact { position: absolute; right: 12px; top: 7px; font-size: 4.2px; line-height: 1.6; color: var(--ink); border-left: 0.5px solid #bbb; padding-left: 3px; }
  .contact .tag { color: var(--red); }
  .ico { color: var(--red); margin-right: 2px; }

  .footer-line { position: absolute; left: 0; width: 100%; text-align: center; font-size: 4.4px; color: var(--ink); }
  .footer-line .tag { color: var(--red); }

  .band { position: absolute; left: 0; width: 100%; height: 8px; background: var(--red); color: #fff; font-size: 5px; text-align: center; line-height: 8px; letter-spacing: 1px; }
  .band::before, .band::after { content: ""; position: absolute; left: 0; width: 100%; height: 0.6px; background: var(--rule); }
  .band::before { top: -3px; } .band::after { bottom: -3px; }
  .sheet .band { top: 323px; }
  .sheet--fax .band { letter-spacing: .2px; font-size: 4.4px; }

  .fax__title { position: absolute; left: 10px; top: 78px; font-size: 16px; font-weight: 300; letter-spacing: .5px; }
  .fax__fields { position: absolute; left: 10px; top: 109px; width: 232px; display: grid; grid-template-columns: 1fr 1fr; column-gap: 16px; row-gap: 8px; }
  .field { font-size: 4.6px; border-bottom: 0.6px solid var(--rule); padding-bottom: 1px; }
  .fax__checks { position: absolute; left: 10px; top: 192px; width: 234px; display: flex; justify-content: space-between; font-size: 4.6px; }
  .check { display: flex; align-items: center; gap: 3px; }
  .check::before { content: ""; width: 5px; height: 5px; border: 0.6px solid var(--rule); }

  .label { position: absolute; top: 360px; width: 262px; text-align: center; font-size: 17px; color: #6a6a6a; }

  .envelopes { position: absolute; left: 838px; top: 4px; width: 340px; height: 252px; }
  .envelope--front { position: absolute; left: 34px; top: 118px; width: 294px; height: 130px; background: linear-gradient(170deg, var(--paper) 50%, var(--paper-shade)); box-shadow: 0 1px 4px rgba(0,0,0,.3); }
  .envelope--front .brand { left: 9px; top: 12px; }
  .envelope--front .brand__dot { width: 26px; height: 26px; }
  .envelope--front .brand__name { font-size: 10px; }
  .envelope__address { position: absolute; left: 42px; top: 43px; font-size: 5px; line-height: 1.5; }
  .envelope--front .band { top: 114px; }

  .card { position: absolute; top: 270px; width: 160px; height: 90px; box-shadow: 0 1px 4px rgba(0,0,0,.3); }
  .card--front { left: 864px; background: var(--paper); }
  .card--back { left: 1032px; background: var(--black); }
  .card--front .brand { left: 34px; top: 11px; }
  .card--front .brand__dot { width: 20px; height: 20px; }
  .card--front .brand__name { font-size: 8px; }
  .card__tagline { top: 47px; height: 7px; line-height: 7px; font-size: 4.6px; font-weight: 600; letter-spacing: .4px; }
  .card__tagline::before { top: -2.5px; } .card__tagline::after { bottom: -2.5px; }
  .card__details { position: absolute; left: 10px; top: 60px; width: 140px; display: grid; grid-template-columns: 1fr 1fr; font-size: 3.9px; line-height: 1.55; }
  .card__company { text-align: right; padding-right: 5px; border-right: 0.5px solid #bbb; }
  .card__company .tag { color: var(--red); font-weight: 600; font-size: 4.4px; }
  .card__phones { padding-left: 5px; }
  .card--back .brand { left: 32px; top: 27px; }
  .card--back .brand__dot { width: 22px; height: 22px; }
  .card--back .brand__name { color: #fff; font-size: 8.4px; }
  .card__web { position: absolute; bottom: 13px; width: 100%; text-align: center; color: #fff; font-size: 4.6px; letter-spacing: 1px; }
</style>
</head>
<body>
<main class="canvas">

  <section class="sheet sheet--plain" aria-label="Letterhead, option 1">
    <div class="brand"><span class="brand__dot"></span><span class="brand__name">MARLOW'S<br>ENTERTAINMENT</span></div>
    <p class="footer-line" style="top:325px"><span class="tag">MARLOW'S LIMITED</span> &nbsp;12, Harbour View Road, Colombo 01000, Sri Lanka</p>
    <p class="footer-line" style="top:332px"><span class="ico">✆</span>+94 11 555 0142 &nbsp;<span class="ico">▪</span>+94 11 555 0100 &nbsp;<span class="ico">✉</span>info@marlowscolombo.com &nbsp;<span class="ico">◉</span>www.marlowscolombo.com</p>
  </section>

  <section class="sheet sheet--letter" aria-label="Letterhead, option 2">
    <div class="brand"><span class="brand__dot"></span><span class="brand__name">MARLOW'S<br>ENTERTAINMENT</span></div>
    <div class="contact">
      <span class="ico">✆</span>+94 11 555 0142<br>
      <span class="ico">▪</span>+94 11 555 0100<br>
      <span class="ico">✉</span>info@marlowscolombo.com<br>
      <span class="tag">MARLOW'S LIMITED</span><br>
      12, Harbour View Road<br>Colombo 01000, Sri Lanka
    </div>
    <div class="band">www.marlowscolombo.com</div>
  </section>

  <section class="sheet sheet--fax" aria-label="Fax sheet, option 3">
    <div class="brand"><span class="brand__dot"></span><span class="brand__name">MARLOW'S<br>ENTERTAINMENT</span></div>
    <div class="contact">
      <span class="ico">✆</span>+94 11 555 0142<br>
      <span class="ico">▪</span>+94 11 555 0100<br>
      <span class="ico">✉</span>info@marlowscolombo.com<br>
      <span class="ico">◉</span>www.marlowscolombo.com
    </div>
    <h1 class="fax__title">FAX</h1>
    <div class="fax__fields">
      <span class="field">To :</span><span class="field">From :</span>
      <span class="field">Fax :</span><span class="field">Pages :</span>
      <span class="field">Phone :</span><span class="field">Date :</span>
      <span class="field">Re :</span><span class="field">CC :</span>
    </div>
    <div class="fax__checks">
      <span class="check">Urgent</span><span class="check">For Review</span><span class="check">Please Comment</span><span class="check">Please Reply</span><span class="check">Please Recycle</span>
    </div>
    <div class="band">MARLOW'S LIMITED &nbsp;12, Harbour View Road, Colombo 01000, Sri Lanka</div>
  </section>

  <p class="label" style="left:8px">Option-1</p>
  <p class="label" style="left:286px">Option-2</p>
  <p class="label" style="left:559px">Option-3</p>

  <div class="envelopes" aria-label="Envelopes">
    <svg width="340" height="200" viewBox="0 0 340 200" style="position:absolute;left:0;top:0">
      <rect class="envelope--back" x="66" y="2" width="272" height="150" fill="#fff" stroke="#999" stroke-width="0.6"/>
      <path d="M66 2 H338 V14 C300 40 230 60 202 64 C174 60 104 40 66 14 Z" fill="#0c0c0c"/>
      <rect x="2" y="58" width="324" height="134" fill="#fbfbfb" stroke="#999" stroke-width="0.6"/>
      <path d="M2 58 C60 76 150 102 164 108 C178 102 268 76 326 58" fill="none" stroke="#444" stroke-width="0.8"/>
    </svg>
    <div class="envelope--front">
      <div class="brand"><span class="brand__dot"></span><span class="brand__name">MARLOW'S<br>ENTERTAINMENT</span></div>
      <p class="envelope__address">12, Harbour View Road<br>Colombo 01000, Sri Lanka</p>
      <div class="band">www.marlowscolombo.com</div>
    </div>
  </div>

  <section class="card card--front" aria-label="Business card, front">
    <div class="brand"><span class="brand__dot"></span><span class="brand__name">MARLOW'S<br>ENTERTAINMENT</span></div>
    <div class="band card__tagline">Highest Winning Percentage In The World</div>
    <div class="card__details">
      <div class="card__company"><span class="tag">MARLOW'S LIMITED</span><br>12, Harbour View Road<br>Colombo 01000<br>Sri Lanka</div>
      <div class="card__phones"><span class="ico">✆</span>+94 11 555 0142<br><span class="ico">▯</span>+94 77 555 0199<br><span class="ico">▪</span>+94 11 555 0100<br><span class="ico">✉</span>info@marlowscolombo.com</div>
    </div>
  </section>

  <section class="card card--back" aria-label="Business card, back">
    <div class="brand"><span class="brand__dot"></span><span class="brand__name">MARLOW'S<br>ENTERTAINMENT</span></div>
    <p class="card__web">www.marlowscolombo.com</p>
  </section>

</main>
</body>
</html>
```